Bramble Hockey Academy

We are are Ice Hockey Development Company that provided on-ice Hockey development services. We need a Landing Page with tabs to direct to individual program pages.
Landing Page
About Page
Winter Program Page
Spring Program Page
Summer Program Page
Team Page
Tournament Page

Coded - Design and coding required

5+ page

```html
<!DOCTYPE html>
<html lang="en">
<head>
<meta charset="utf-8">
<title>Bramble Hockey Academy</title>
<link rel="stylesheet" href="https://fonts.googleapis.com/css2?family=Poppins:wght@400;500;600;700;800&family=Montserrat:wght@400;500;600;700&family=Kaushan+Script&display=swap">
<style>
:root{
  --green:#0f5c0b;
  --green-dark:#0a3a08;
  --green-deep:#082a07;
  --yellow:#f3e516;
  --red:#d8232a;
  --mint:#c8f3c2;
  --ink:#161616;
  --grey-card:rgba(150,150,150,.55);
}
*{box-sizing:border-box;margin:0;padding:0}
html,body{width:1200px;height:5168px;overflow:hidden}
body{font-family:'Poppins',sans-serif;color:var(--ink);background:#fff;position:relative}
.abs{position:absolute}
section,header,footer{position:absolute;left:0;width:1200px;overflow:hidden}
.btn{position:absolute;display:flex;align-items:center;justify-content:center;font-weight:600;white-space:nowrap}

/* hero */
.hero{top:0;height:636px;background:linear-gradient(180deg,#0d1f2e 0%,#1b3a55 38%,#3f6583 60%,#9fb8c9 80%,#d5e2ea 100%)}
.hero-beams{position:absolute;inset:0;background:
  linear-gradient(100deg,rgba(255,255,255,0) 30%,rgba(200,225,255,.18) 38%,rgba(255,255,255,0) 46%),
  linear-gradient(80deg,rgba(255,255,255,0) 52%,rgba(200,225,255,.16) 60%,rgba(255,255,255,0) 68%),
  radial-gradient(ellipse at 50% 0%,rgba(220,235,255,.45) 0%,rgba(255,255,255,0) 45%)}
.hero-action{position:absolute;left:330px;top:70px;width:520px;height:566px;background:
  radial-gradient(ellipse 34% 22% at 44% 28%,rgba(35,75,190,.95) 0%,rgba(35,75,190,0) 100%),
  radial-gradient(ellipse 26% 20% at 66% 40%,rgba(190,30,40,.9) 0%,rgba(190,30,40,0) 100%),
  radial-gradient(ellipse 30% 30% at 55% 62%,rgba(20,20,25,.85) 0%,rgba(20,20,25,0) 100%),
  radial-gradient(ellipse 40% 8% at 55% 96%,rgba(255,255,255,.7) 0%,rgba(255,255,255,0) 100%)}
.boards{position:absolute;left:0;top:440px;width:1200px;height:10px;background:rgba(255,255,255,.35)}
.logo-box{position:absolute;left:75px;top:0;width:190px;height:92px;background:#fff;display:flex;align-items:center;justify-content:center;font-weight:800;font-size:22px;color:var(--green-deep);line-height:1;text-align:center}
.topbar{position:absolute;top:10px;font-size:9px;color:#fff;white-space:nowrap}
.topbar .gold{color:var(--yellow);margin-right:8px}
.live{position:absolute;left:702px;top:8px;background:var(--red);color:#fff;font-size:9px;font-weight:700;padding:2px 8px}
.nav{position:absolute;top:58px;left:315px;font-size:12px;color:#fff;font-weight:500}
.nav span{position:absolute;white-space:nowrap}
.countdown-num{position:absolute;left:136px;top:270px;width:96px;height:114px;background:var(--yellow);color:var(--red);font-size:90px;font-weight:800;display:flex;align-items:center;justify-content:center}
.countdown-text{position:absolute;left:232px;top:286px;width:608px;height:78px;background:var(--green);color:#fff;font-size:39px;font-weight:700;padding-left:6px;display:flex;align-items:center;white-space:nowrap}
.match{position:absolute;left:136px;top:400px;height:58px;display:flex;font-weight:700;font-size:25px;white-space:nowrap}
.match .home{background:var(--green);color:#fff;width:160px;display:flex;align-items:center;justify-content:flex-end;padding-right:6px}
.match .vs{width:54px;background:linear-gradient(90deg,var(--green) 50%,var(--yellow) 50%);color:var(--red);font-size:36px;font-weight:800;display:flex;align-items:center;justify-content:center}
.match .away{background:var(--yellow);color:var(--red);width:176px;display:flex;align-items:center;padding-left:6px}
.next{position:absolute;left:1016px;top:316px;width:132px;height:124px;background:var(--yellow);color:var(--red);font-weight:700;font-size:33px;display:flex;align-items:center;justify-content:center}

.breaking{top:636px;height:98px;background:var(--green)}
.breaking .tag{position:absolute;left:0;top:0;width:382px;height:98px;background:var(--yellow);color:var(--red);font-size:35px;font-weight:700;display:flex;align-items:center;padding-left:48px}
.breaking p{position:absolute;left:400px;top:36px;color:#fff;font-size:18px}

/* tournaments */
.ice-bg{background:radial-gradient(ellipse at 30% 40%,#f7f8f9 0%,#dfe3e6 55%,#cfd4d8 100%)}
.tournaments{top:734px;height:578px}
.sec-title{position:absolute;width:1200px;text-align:center;font-weight:700;font-size:33px;letter-spacing:.5px}
.t-card{position:absolute;top:114px;width:354px;height:420px}
.t-photo{position:absolute;left:0;top:0;width:354px;height:192px;background:
  radial-gradient(ellipse 30% 40% at 75% 40%,rgba(25,40,30,.8) 0%,rgba(25,40,30,0) 100%),
  radial-gradient(ellipse 25% 35% at 20% 35%,rgba(25,40,30,.7) 0%,rgba(25,40,30,0) 100%),
  linear-gradient(180deg,#5d7a69 0%,#8fa79b 60%,#c6d3cd 100%)}
.t-name{position:absolute;left:0;top:52px;width:354px;text-align:center;color:#fff;font-size:35px;font-weight:700;line-height:40px;text-shadow:0 2px 6px rgba(0,0,0,.4)}
.t-script{position:absolute;left:0;top:134px;width:354px;text-align:center;font-family:'Kaushan Script',cursive;color:var(--yellow);font-size:34px}
.t-meta{position:absolute;left:0;top:192px;width:354px;height:56px;background:var(--yellow);display:flex;align-items:center;justify-content:center;font-weight:700;font-size:23px;white-space:nowrap}
.t-meta .sep{width:2px;height:30px;background:var(--ink);margin:0 18px}
.t-meta .city{color:var(--red)}
.t-body{position:absolute;left:0;top:248px;width:354px;height:172px;background:var(--green-deep)}
.t-fee{position:absolute;top:44px;width:354px;text-align:center;color:#fff;font-weight:700;font-size:23px}
.t-reg{left:60px;top:82px;width:112px;height:46px;background:var(--yellow);color:var(--red);font-size:16px}
.t-view{left:188px;top:82px;width:112px;height:46px;border:2px solid #fff;color:#fff;font-size:16px}

/* result */
.result{top:1312px;height:456px;background:radial-gradient(ellipse at 50% 45%,#e8eaec 0%,#b8bdc2 30%,#4a5560 55%,#15181b 100%)}
.result-floor{position:absolute;left:0;bottom:0;width:1200px;height:110px;background:linear-gradient(180deg,rgba(20,80,40,0) 0%,#0f4a1c 100%)}
.flood{position:absolute;top:20px;width:200px;height:160px;background:radial-gradient(ellipse at 50% 50%,rgba(255,255,255,.95) 0%,rgba(220,230,255,.5) 30%,rgba(255,255,255,0) 70%)}
.helmet{position:absolute;top:150px;width:270px;height:220px;border-radius:52% 48% 40% 45%}
.score{position:absolute;top:170px;width:120px;text-align:center;font-size:120px;font-weight:800;color:#111;line-height:1}
.team-name{position:absolute;top:310px;width:200px;text-align:center;font-size:29px;font-weight:600;color:#111;white-space:nowrap}

/* events */
.events{top:1768px;height:632px;background:
  radial-gradient(ellipse 25% 40% at 35% 30%,rgba(230,230,230,.25) 0%,rgba(0,0,0,0) 100%),
  radial-gradient(ellipse 25% 40% at 75% 45%,rgba(200,160,60,.25) 0%,rgba(0,0,0,0) 100%),
  linear-gradient(160deg,#2f3a31 0%,#19241b 40%,#3a4a3c 100%)}
.ev-title{position:absolute;top:40px;color:#fff;font-size:33px;font-weight:700}
.ev-sub{position:absolute;top:100px;color:var(--yellow);font-size:20px;font-weight:500}
.ev-row{position:absolute;width:516px;height:122px;background:var(--grey-card)}
.avatar{position:absolute;left:24px;top:22px;width:78px;height:78px;border-radius:50%;background:radial-gradient(circle at 50% 40%,#c98b7a 0%,#8a2a35 50%,#3a1216 100%)}
.ev-row .label{position:absolute;left:122px;top:46px;color:#fff;font-size:21px;font-weight:500;white-space:nowrap}
.ev-more{left:350px;top:38px;width:128px;height:48px;background:var(--green);color:#fff;font-size:19px;font-weight:500}
.badge{position:absolute;top:26px;width:70px;height:70px;border-radius:50%;background:var(--yellow);border:5px solid #b81c25}
.fx-league{position:absolute;top:14px;width:516px;text-align:center;color:#fff;font-size:11px}
.fx-score{position:absolute;top:28px;width:516px;text-align:center;color:#fff;font-size:50px;font-weight:700;line-height:60px}
.fx-date{position:absolute;top:90px;width:516px;text-align:center;color:#fff;font-size:12px}

/* stats */
.stats{top:2400px;height:160px;background:var(--mint)}
.stat{position:absolute;top:42px;display:flex;align-items:center;gap:14px}
.stat .n{font-size:38px;font-weight:700;color:var(--red);line-height:1}
.stat .l{font-size:11px;color:#222;white-space:nowrap}
.stat svg{width:50px;height:58px}

/* team */
.team{top:2560px;height:670px}
.team-curve{position:absolute;top:0;left:0}
.kicker{position:absolute;color:var(--red);font-size:20px}
.h2{position:absolute;font-weight:700;font-size:35px}
.num83{position:absolute;left:48px;top:160px;width:82px;height:80px;background:var(--green);color:#fff;font-size:47px;font-weight:700;display:flex;align-items:center;justify-content:center}
.player-name{position:absolute;left:145px;top:160px;font-size:50px;font-weight:600;color:var(--green);line-height:80px;white-space:nowrap}
.copy{position:absolute;font-size:15.5px;line-height:23px;color:#333;font-family:'Montserrat',sans-serif}
.yellow-btn{background:var(--yellow);color:var(--red);font-size:17px;border-bottom:4px solid var(--ink)}
.frame-photo{position:absolute}

/* news */
.news{top:3230px;height:576px;background:var(--mint)}
.news-card{position:absolute;top:200px;width:346px;height:326px;background:#fff}
.news-photo{position:absolute;left:0;top:0;width:346px;height:194px}
.news-card h3{position:absolute;left:26px;top:210px;width:300px;font-size:14.5px;font-weight:600;line-height:18px}
.news-card p{position:absolute;left:26px;top:246px;width:296px;font-size:10.5px;line-height:15px;color:#333}
.news-card .more{position:absolute;right:30px;bottom:14px;color:var(--red);font-size:11px;background:#fff;padding-left:6px}
.arrow{position:absolute;width:28px;height:28px;border-radius:50%;display:flex;align-items:center;justify-content:center}

/* partners */
.partners{top:3806px;height:272px;background:radial-gradient(ellipse at 50% 50%,#1b5a16 0%,#0e3a0b 60%,#082708 100%)}
.partner{position:absolute;top:136px;color:#fff;font-weight:700;font-size:26px;text-align:center;white-space:nowrap}

/* about */
.about{top:4078px;height:622px;background:#fff}
.about-title{position:absolute;left:630px;top:70px;color:var(--green);font-weight:700;font-size:46px}
.watermark{position:absolute;left:575px;top:252px;font-size:80px;font-weight:800;color:rgba(0,0,0,.05);line-height:80px;white-space:nowrap}

/* footer */
.footer{top:4700px;height:468px;background:radial-gradient(ellipse at 40% 40%,#205a1a 0%,#0f3a0c 55%,#072505 100%)}
.footer .lab{position:absolute;left:542px;color:var(--yellow);font-size:14px}
.footer .val{position:absolute;left:614px;color:#fff;font-size:9px;line-height:13px;white-space:nowrap}
.social{position:absolute;top:4988px;width:32px;height:32px;border-radius:50%;background:var(--yellow)}
.bottom-links{position:absolute;top:5140px;right:50px;display:flex;gap:18px;color:#fff;font-size:10px}
</style>
</head>
<body>

<header class="hero">
  <div class="hero-beams"></div>
  <div class="boards"></div>
  <div class="hero-action" role="img" aria-label="Two ice hockey players in blue and red battling for the puck under arena lights"></div>
  <div class="logo-box">BRAMBLE<br>HOCKEY</div>
  <div class="topbar" style="left:305px"><span class="gold">GET TICKETS</span>Shop</div>
  <div class="live">LIVE</div>
  <div class="topbar" style="left:760px">Lorem ipsum dolor sit amet, consectetur</div>
  <div class="topbar" style="left:1040px">Sign Up / Sign In</div>
  <nav class="nav">
    <span style="left:0;color:var(--yellow)">HOME</span>
    <span style="left:70px">ABOUT</span>
    <span style="left:150px">WINTER PROGRAM</span>
    <span style="left:300px">SUMMER PROGRAM</span>
    <span style="left:455px">SPRING PROGRAM</span>
    <span style="left:605px">TOURNAMENT</span>
    <span style="left:728px">TEAM</span>
  </nav>
  <div class="countdown-num">2</div>
  <div class="countdown-text">days until the next match</div>
  <div class="match"><div class="home">The Tiger</div><div class="vs">VS</div><div class="away">Red Hawks</div></div>
  <div class="next">Next</div>
</header>

<section class="breaking">
  <div class="tag">Breaking News</div>
  <p>Lorem ipsum dolor sit amet, consectetur adipiscing elit. Sed fringilla</p>
</section>

<section class="tournaments ice-bg">
  <h2 class="sec-title" style="top:38px">OUR TOURNAMENT</h2>
  <article class="t-card" style="left:50px">
    <div class="t-photo" role="img" aria-label="Youth players skating in a summer tournament game"></div>
    <div class="t-name">Summer<br>Ice Hockey</div>
    <div class="t-script">Tournament</div>
    <div class="t-meta"><span>6-8 APRIL</span><span class="sep"></span><span class="city">Vienna City</span></div>
    <div class="t-body"><div class="t-fee">Entry Fee: $70</div><div class="btn t-reg">Register</div><div class="btn t-view">View All</div></div>
  </article>
  <article class="t-card" style="left:423px">
    <div class="t-photo" role="img" aria-label="Winter tournament players in front of the net"></div>
    <div class="t-name">Winter<br>Ice Hockey</div>
    <div class="t-script">Tournament</div>
    <div class="t-meta"><span>6-8 NOV</span><span class="sep"></span><span class="city">Vienna City</span></div>
    <div class="t-body"><div class="t-fee">Entry Fee: $170</div><div class="btn t-reg">Register</div><div class="btn t-view">View All</div></div>
  </article>
  <article class="t-card" style="left:795px">
    <div class="t-photo" role="img" aria-label="Young player in green skating during a spring tournament"></div>
    <div class="t-name">Spring<br>Ice Hockey</div>
    <div class="t-script">Tournament</div>
    <div class="t-meta"><span>6-8 FEB</span><span class="sep"></span><span class="city">Vienna City</span></div>
    <div class="t-body"><div class="t-fee">Entry Fee: $150</div><div class="btn t-reg">Register</div><div class="btn t-view">View All</div></div>
  </article>
</section>

<section class="result">
  <div class="flood" style="left:0"></div>
  <div class="flood" style="left:1000px"></div>
  <div class="result-floor"></div>
  <div class="helmet" role="img" aria-label="Red hockey helmet with a star" style="left:60px;background:radial-gradient(ellipse at 38% 30%,#ff8a8a 0%,#d61d25 40%,#7a070c 85%,rgba(80,5,8,0) 100%)"></div>
  <div class="helmet" role="img" aria-label="Blue hockey helmet with a star" style="left:870px;background:radial-gradient(ellipse at 62% 30%,#9ccaff 0%,#2270e0 40%,#0c2a78 85%,rgba(10,31,90,0) 100%)"></div>
  <h2 class="sec-title" style="top:48px;font-size:30px;color:#111">LATEST RESULT</h2>
  <div class="abs" style="top:94px;width:1200px;text-align:center;font-size:17px;color:#333">GREAT WIN IN FINALS</div>
  <div class="abs" style="top:120px;width:1200px;text-align:center;font-size:12px;color:#444">Fri 27th Jan Champion League</div>
  <div class="score" style="left:428px">2</div>
  <div class="abs" style="left:599px;top:180px;width:2px;height:110px;background:#333"></div>
  <div class="score" style="left:650px">2</div>
  <div class="team-name" style="left:388px">The Tiger</div>
  <div class="team-name" style="left:610px">Red Hawks</div>
  <div class="btn" style="left:528px;top:374px;width:144px;height:40px;background:var(--yellow);color:var(--red);font-size:17px">See More Info</div>
</section>

<section class="events" role="img" aria-label="Dim background of players on the ice">
  <h2 class="ev-title" style="left:48px">Upcoming Events</h2>
  <div class="ev-sub" style="left:48px">What's Next This Month</div>
  <h2 class="ev-title" style="left:630px">Featured Tournaments</h2>
  <div class="ev-sub" style="left:630px">Results</div>
  <div class="ev-row" style="left:48px;top:168px"><div class="avatar" role="img" aria-label="Player portrait"></div><div class="label">Lorem ipsum dolor</div><div class="btn ev-more">See More</div></div>
  <div class="ev-row" style="left:48px;top:318px"><div class="avatar" role="img" aria-label="Player portrait"></div><div class="label">Lorem ipsum dolor</div><div class="btn ev-more">See More</div></div>
  <div class="ev-row" style="left:48px;top:466px"><div class="avatar" role="img" aria-label="Player portrait"></div><div class="label">Lorem ipsum dolor</div><div class="btn ev-more">See More</div></div>
  <div class="ev-row" style="left:632px;top:168px"><div class="badge" style="left:44px"></div><div class="badge" style="left:400px"></div><div class="fx-league">Icehockey League</div><div class="fx-score">8:3</div><div class="fx-date">23rd Mar 2023/ 17 UTC</div></div>
  <div class="ev-row" style="left:632px;top:318px"><div class="badge" style="left:44px"></div><div class="badge" style="left:400px"></div><div class="fx-league">Icehockey League</div><div class="fx-score">8:3</div><div class="fx-date">23rd Mar 2023/ 17 UTC</div></div>
  <div class="ev-row" style="left:632px;top:466px"><div class="badge" style="left:44px"></div><div class="badge" style="left:400px"></div><div class="fx-league">Icehockey League</div><div class="fx-score">8:3</div><div class="fx-date">23rd Mar 2023/ 17 UTC</div></div>
</section>

<section class="stats">
  <div class="stat" style="left:182px">
    <svg viewBox="0 0 50 58" fill="none" stroke="var(--green)" stroke-width="2.5"><path d="M15 6 L5 14 L10 24 L14 22 L14 52 L36 52 L36 22 L40 24 L45 14 L35 6 Q25 14 15 6Z"/><text x="25" y="40" font-size="12" text-anchor="middle" fill="var(--green)" stroke="none" font-weight="700">10</text></svg>
    <div><div class="n">12k</div><div class="l">Lorem ipsum dolor</div></div>
  </div>
  <div class="stat" style="left:424px">
    <svg viewBox="0 0 50 58" fill="none" stroke="var(--green)" stroke-width="2.5"><path d="M13 6 H37 V20 Q37 34 25 34 Q13 34 13 20Z"/><path d="M13 10 H5 Q5 22 14 24 M37 10 H45 Q45 22 36 24"/><path d="M25 34 V44 M15 52 H35 V44 H15Z"/></svg>
    <div><div class="n">65</div><div class="l">Lorem ipsum dolor</div></div>
  </div>
  <div class="stat" style="left:664px">
    <svg viewBox="0 0 50 58" fill="none" stroke="var(--green)" stroke-width="2.5"><path d="M14 4 L22 24 M36 4 L28 24 M14 4 H36"/><circle cx="25" cy="38" r="14"/><circle cx="25" cy="38" r="7"/></svg>
    <div><div class="n">4</div><div class="l">Lorem ipsum dolor</div></div>
  </div>
  <div class="stat" style="left:874px">
    <svg viewBox="0 0 50 58" fill="none" stroke="var(--green)" stroke-width="2.5"><path d="M8 4 L34 46 Q38 52 46 50 L46 44 L38 44 M42 4 L16 46 Q12 52 4 50 L4 44 L12 44"/></svg>
    <div><div class="n">19</div><div class="l">Lorem ipsum dolor</div></div>
  </div>
</section>

<section class="team ice-bg">
  <svg class="team-curve" width="1200" height="40" viewBox="0 0 1200 40"><path d="M0 0 H1200 V6 Q600 14 0 34Z" fill="var(--green-deep)"/></svg>
  <h2 class="h2" style="left:48px;top:42px">Our Team</h2>
  <div class="kicker" style="left:48px;top:92px">Player of The Month</div>
  <div class="num83">83</div>
  <div class="player-name">Jenna Ashby</div>
  <p class="copy" style="left:48px;top:264px;width:630px">Lorem ipsum dolor sit amet, consectetur adipiscing elit. Sed fringilla urna congue orci pharetra commodo. Fusce nec nulla turpis. Proin vehicula justo ut sem pulvinar, iaculis iaculis nisl imperdiet. Ut diam erat, gravida vitae sagittis ac, tincidunt et mauris. Nam ante sapien, commodo eu nibh nec, malesuada vulputate magna. Sed eros enim, dictum a dui quis, varius finibus erat. Nullam vulputate rhoncus sem quis ultrices.</p>
  <p class="copy" style="left:48px;top:424px;width:630px">Donec aliquam nunc at dui pellentesque hendrerit. Fusce sodales consectetur orci, vel tempus turpis vulputate sed. Phasellus vestibulum quam dui, non ultrices eros lobortis a. Ut interdum non nunc non semper. Donec eget purus interdum, congue felis sit amet, imperdiet tellus. Sed ut magna semper dolor vulputate posuere eget nec nulla. Sed vitae efficitur tortor, at bibendum metus. Aliquam consectetur ipsum eget mi imperdiet porta.</p>
  <div class="btn yellow-btn" style="left:48px;top:598px;width:136px;height:52px">View All</div>
  <div class="abs" style="left:712px;top:140px;width:436px;height:520px;background:var(--green-deep)"></div>
  <div class="frame-photo" role="img" aria-label="Player of the month seated in a maroon jersey holding a stick" style="left:728px;top:152px;width:408px;height:500px;background:
    radial-gradient(ellipse 22% 12% at 50% 22%,rgba(220,170,140,.9) 0%,rgba(220,170,140,0) 100%),
    radial-gradient(ellipse 38% 30% at 50% 50%,rgba(130,20,35,.95) 0%,rgba(130,20,35,0) 100%),
    radial-gradient(ellipse 30% 22% at 50% 78%,rgba(20,22,35,.9) 0%,rgba(20,22,35,0) 100%),
    radial-gradient(ellipse at 50% 40%,#7a5532 0%,#4a321c 55%,#2a1d11 100%)"></div>
  <div class="abs" style="left:736px;top:188px;width:372px;height:450px;border:2px solid #2fa52a"></div>
</section>

<section class="news">
  <h2 class="sec-title" style="top:86px;font-size:35px;font-weight:600">Tournament News</h2>
  <div class="abs" style="top:140px;width:1200px;text-align:center;color:var(--red);font-size:20px">What's next this month</div>
  <div class="arrow" style="left:14px;top:386px;background:#666"><svg width="12" height="12" viewBox="0 0 12 12"><path d="M8 2 L4 6 L8 10" stroke="#fff" stroke-width="2" fill="none"/></svg></div>
  <div class="arrow" style="left:1158px;top:386px;background:#111"><svg width="12" height="12" viewBox="0 0 12 12"><path d="M4 2 L8 6 L4 10" stroke="#fff" stroke-width="2" fill="none"/></svg></div>
  <article class="news-card" style="left:48px">
    <div class="news-photo" role="img" aria-label="Player in red skating in a lit arena" style="background:radial-gradient(ellipse 18% 35% at 50% 55%,rgba(200,30,40,.85) 0%,rgba(200,30,40,0) 100%),radial-gradient(ellipse at 50% 80%,#a9c0d8 0%,#3a5577 50%,#111a28 100%)"></div>
    <h3>Welcome MVA's Executive Director!</h3>
    <p>On behalf of the Board, it gives me great pleasure to announce the selection of Dale Morrow as MVA's Executive Director.</p>
    <span class="more">Read More ⟶</span>
  </article>
  <article class="news-card" style="left:426px">
    <div class="news-photo" role="img" aria-label="Two players contesting the puck during a game" style="background:radial-gradient(ellipse 16% 30% at 42% 50%,rgba(230,200,30,.85) 0%,rgba(230,200,30,0) 100%),radial-gradient(ellipse 16% 30% at 60% 50%,rgba(20,20,20,.85) 0%,rgba(20,20,20,0) 100%),radial-gradient(ellipse at 50% 70%,#8fa6bd 0%,#2b3f5a 60%,#121b28 100%)"></div>
    <h3>2022 MVA Annual General Meeting</h3>
    <p>At the end of each season, MVA holds its Annual General Meeting where our Zone Directors meet to discuss</p>
    <span class="more">Read More ⟶</span>
  </article>
  <article class="news-card" style="left:802px">
    <div class="news-photo" role="img" aria-label="Skater spraying ice in a misty rink" style="background:radial-gradient(ellipse 16% 30% at 50% 50%,rgba(200,30,50,.8) 0%,rgba(200,30,50,0) 100%),radial-gradient(ellipse at 50% 50%,#f2f4f6 0%,#c9d0d6 60%,#9aa5ae 100%)"></div>
    <h3>MVA and Riverbend Brewing Announce Partnership!</h3>
    <p style="top:264px">Bramble Hockey Academy and Riverbend Brewing are excited to announce a new partnership! MVA Members will now be able</p>
    <span class="more">Read More ⟶</span>
  </article>
</section>

<section class="partners">
  <h2 class="sec-title" style="top:36px;color:#fff;font-size:33px;font-weight:600">Our Partners</h2>
  <div class="arrow" style="left:14px;top:130px;background:#ccc"><svg width="12" height="12" viewBox="0 0 12 12"><path d="M8 2 L4 6 L8 10" stroke="#333" stroke-width="2" fill="none"/></svg></div>
  <div class="arrow" style="left:1158px;top:130px;background:#fff"><svg width="12" height="12" viewBox="0 0 12 12"><path d="M4 2 L8 6 L4 10" stroke="#333" stroke-width="2" fill="none"/></svg></div>
  <div class="partner" style="left:60px;width:200px">Northcap</div>
  <div class="partner" style="left:290px;width:240px">Cedarline Grill</div>
  <div class="partner" style="left:620px;width:260px">Riverbend Brewing</div>
  <div class="partner" style="left:880px;width:240px">Hartwell Sports</div>
</section>

<section class="about">
  <div class="abs" style="left:68px;top:32px;width:416px;height:546px;background:var(--green-deep)"></div>
  <div class="frame-photo" role="img" aria-label="Player in a white jersey and maroon helmet skating with a stick" style="left:68px;top:32px;width:400px;height:530px;background:
    radial-gradient(ellipse 14% 9% at 45% 18%,rgba(110,25,35,.95) 0%,rgba(110,25,35,0) 100%),
    radial-gradient(ellipse 30% 26% at 48% 45%,rgba(255,255,255,.95) 0%,rgba(255,255,255,0) 100%),
    radial-gradient(ellipse 26% 22% at 50% 75%,rgba(60,30,30,.7) 0%,rgba(60,30,30,0) 100%),
    linear-gradient(180deg,#a89b8f 0%,#d9d6d2 55%,#eef1f3 100%)"></div>
  <div class="abs" style="left:72px;top:72px;width:376px;height:446px;border:2px solid #2fa52a"></div>
  <div class="watermark">BRAMBLE<br>HOCKEY</div>
  <h2 class="about-title">ABOUT US</h2>
  <p class="copy" style="left:630px;top:140px;width:520px">Lorem ipsum dolor sit amet, consectetur adipiscing elit. Sed fringilla urna congue orci pharetra commodo. Fusce nec nulla turpis. Proin vehicula justo ut sem pulvinar, iaculis iaculis nisl imperdiet. Ut diam erat, gravida vitae sagittis ac, tincidunt et mauris. Nam ante sapien, commodo eu nibh nec, malesuada vulputate magna. Sed eros enim, dictum a dui quis, varius finibus erat. Nullam vulputate rhoncus sem quis ultrices.</p>
  <p class="copy" style="left:630px;top:334px;width:520px">Donec aliquam nunc at dui pellentesque hendrerit. Fusce sodales consectetur orci, vel tempus turpis vulputate sed. Phasellus vestibulum quam dui, non ultrices eros lobortis a. Ut interdum non nunc non semper.</p>
  <div class="btn yellow-btn" style="left:630px;top:450px;width:136px;height:52px">Learn More</div>
</section>

<footer class="footer">
  <div class="abs" role="img" aria-label="Player in a white jersey skating with a stick" style="left:70px;top:30px;width:260px;height:390px;background:
    radial-gradient(ellipse 16% 8% at 45% 12%,rgba(120,25,35,.9) 0%,rgba(120,25,35,0) 100%),
    radial-gradient(ellipse 34% 24% at 48% 38%,rgba(245,245,245,.9) 0%,rgba(245,245,245,0) 100%),
    radial-gradient(ellipse 28% 26% at 50% 72%,rgba(190,40,50,.6) 0%,rgba(190,40,50,0) 100%)"></div>
  <div class="abs" style="left:534px;top:80px;width:120px;height:120px;border-radius:50%;background:#fff;display:flex;align-items:center;justify-content:center;font-weight:800;font-size:16px;color:var(--green-deep);text-align:center;line-height:1.05">BRAMBLE<br>HOCKEY</div>
  <span class="lab" style="top:210px">Address</span>
  <span class="val" style="top:210px">Unit 4, 22 Larch Street<br>Millbrook, ON K0L 2T0</span>
  <span class="lab" style="top:262px">Phone</span>
  <span class="val" style="top:265px">(555) 014-2290</span>
  <span class="lab" style="top:308px">Fax</span>
  <span class="val" style="top:311px">(555) 014-2291</span>
  <div class="abs" style="left:770px;top:162px;color:var(--yellow);font-size:19px">Subscribe To Newsletter</div>
  <div class="abs" style="left:770px;top:204px;width:176px;height:50px;background:#0a1d08;color:#fff;font-size:10px;padding:19px 0 0 24px">Enter Your Email</div>
  <div class="btn" style="left:946px;top:204px;width:132px;height:50px;background:var(--yellow);color:var(--red);font-size:15px">SUBSCRIBE</div>
  <div class="abs" style="left:75px;top:440px;color:#fff;font-size:10px">Copyright Bramble Hockey Academy©. All Rights Reserve</div>
</footer>
<span class="social" style="left:772px" aria-label="Social link"></span>
<span class="social" style="left:822px" aria-label="Social link"></span>
<span class="social" style="left:870px" aria-label="Social link"></span>
<span class="social" style="left:924px" aria-label="Social link"></span>
<div class="bottom-links"><span>Home</span><span>About</span><span>Tournament</span><span>Team</span><span>Summer Program</span><span>Winter Program</span><span>Spring Program</span></div>

</body>
</html>
```